New business card/stationary for a consulting company

I am looking for a clean and very professional looking business card for my consulting company as well as corresponding stationary. I am uploading our logo. I like simple and powerful for the feel. No graphics but I am open on everything else. Below is my contact information but would like the final to be in a version I can add my employees information into and print. Thank you.

Daniel Whitcombe
dan@ferncliffadvisory.com
2870 North 9th Avenue, Summit Floor, Elm Ridge, Illinois 60531
www.ferncliffadvisory.com

Industry/Entity Type

Consulting

Contact Information for Business Card

Daniel Whitcombe
dan@ferncliffadvisory.com
www.ferncliffadvisory.com

Font styles to use
Serif
Sans Serif

Requirements
Must have
• Our logo and the business card details.
Nice to have
• our website www.ferncliffadvisory.com

```html
<!DOCTYPE html>
<html lang="en">
<head>
<meta charset="utf-8">
<title>Ferncliff Advisory — Business Card</title>
<link rel="stylesheet" href="https://fonts.googleapis.com/css2?family=Questrial&family=Open+Sans:wght@400;600&display=swap">
<style>
  :root {
    --navy: #1f1b6b;
    --navy-deep: #221e63;
    --silver: #c9c9cc;
    --rule: #b9b9b9;
    --ink: #3a3a3a;
    --paper: #ffffff;
    --backdrop: #e8e6e3;
  }
  * { box-sizing: border-box; margin: 0; padding: 0; }
  html, body {
    width: 1200px; height: 900px; overflow: hidden;
    background: var(--backdrop);
  }
  .sheet {
    position: relative; width: 1200px; height: 900px;
    display: flex; align-items: center; justify-content: center; gap: 60px;
  }
  .card {
    width: 520px; height: 298px;
    box-shadow: 0 2px 8px rgba(0,0,0,0.12);
    display: flex; flex-direction: column; align-items: center; justify-content: center;
  }
  .card--front { background: var(--paper); padding: 0 36px; }
  .card--back { background: var(--navy-deep); }

  .brand {
    display: flex; align-items: center; gap: 12px;
    font-family: "Questrial", sans-serif;
    letter-spacing: 0.06em; text-transform: uppercase; white-space: nowrap;
  }
  .brand__mark { width: 20px; height: 20px; }
  .card--front .brand { color: var(--navy); font-size: 29px; }
  .card--front .brand__mark { background: var(--navy); }
  .card--back .brand { color: var(--silver); font-size: 29px; }
  .card--back .brand__mark { background: var(--silver); }

  .person {
    display: flex; align-items: center; gap: 14px; width: 100%;
    margin-top: 18px;
  }
  .person__rule { flex: 1; height: 1.5px; background: var(--rule); }
  .person__name {
    font-family: "Questrial", sans-serif; color: var(--navy);
    font-size: 17px; letter-spacing: 0.05em; text-transform: uppercase; white-space: nowrap;
  }
  .contact {
    margin-top: 12px;
    font-family: "Open Sans", sans-serif; font-size: 13px; color: var(--ink); line-height: 1.45;
  }
  .contact__label { color: var(--navy); font-weight: 600; }
  .address {
    margin-top: 14px; text-align: center;
    font-family: "Open Sans", sans-serif; font-size: 13px; color: var(--ink); line-height: 1.45;
  }
</style>
</head>
<body>
  <main class="sheet">
    <section class="card card--front" aria-label="Business card front">
      <div class="brand"><span class="brand__mark"></span><span class="brand__name">Ferncliff Advisory</span></div>
      <div class="person">
        <span class="person__rule"></span>
        <span class="person__name">Daniel Whitcombe</span>
        <span class="person__rule"></span>
      </div>
      <div class="contact">
        <p><span class="contact__label">E:</span> dan@ferncliffadvisory.com</p>
        <p><span class="contact__label">W:</span> www.ferncliffadvisory.com</p>
      </div>
      <p class="address">2870 North 9th Avenue,<br>Summit Floor, Elm Ridge, Illinois 60531</p>
    </section>

    <section class="card card--back" aria-label="Business card back">
      <div class="brand"><span class="brand__mark"></span><span class="brand__name">Ferncliff Advisory</span></div>
    </section>
  </main>
</body>
</html>
```